Brightmoor Lift Inc Website Deisgn

We are a new small elevator contracting company.
We would like a full website designed similar to
http://pellingtonlifts.com or https://www.northvalelifting.ca/
In addition to contents found on the above webpages.. we would like a section for project gallery etc.... have fun with it ... make it professional

Target Market(s)

Elevator Consultants - Property managers - Condo Boards - Commercial office buildings

Coding

Number of Pages Required

5+ page

Requirements
Must have
• Navigation Bar.. Be view able via mobile ..Should be pictures of Tall Office buildings in background.. Toronto city skyline etc....

Have Fun!

```html
<!DOCTYPE html>
<html lang="en">
<head>
<meta charset="utf-8">
<title>Brightmoor Lift Inc</title>
<link rel="stylesheet" href="https://fonts.googleapis.com/css2?family=Oswald:wght@500;600&family=Roboto:wght@300;400;500;700&display=swap">
<style>
:root{
  --blue:#0d5fd0;
  --blue-dark:#0a4aa8;
  --ink:#1d1d1d;
  --text:#555;
  --pale:#eaf4fe;
  --dark:#2b2d31;
  --white:#fff;
}
*{box-sizing:border-box;margin:0;padding:0}
html,body{width:1200px;height:5263px;overflow:hidden;background:var(--white)}
body{position:relative;font-family:"Roboto",sans-serif;color:var(--ink)}
.abs{position:absolute}
.heading{font-family:"Oswald",sans-serif;font-weight:600;text-transform:uppercase;color:var(--ink);letter-spacing:.5px}
.lead{font-size:15px;font-weight:300;color:var(--text);line-height:27px;text-align:center}
.btn{position:absolute;display:flex;align-items:center;justify-content:space-between;background:var(--blue);color:var(--white);border-radius:30px;font-family:"Oswald",sans-serif;font-weight:500;font-size:17px;text-transform:uppercase;padding:0 6px 0 30px;letter-spacing:.3px;white-space:nowrap}
.btn .ring{width:38px;height:38px;border-radius:50%;border:3px solid var(--white);background:var(--blue)}
/* header */
.brand{left:78px;top:28px;display:flex;align-items:center;gap:8px;font-family:"Oswald",sans-serif;font-weight:600;font-size:28px;color:var(--ink);white-space:nowrap}
.brand .dot{width:34px;height:34px;border-radius:50%;background:var(--ink)}
.nav{left:523px;top:36px;display:flex;gap:22px;font-size:14px;color:var(--ink);font-weight:400}
.nav a{color:inherit;text-decoration:none}
.nav .active{color:var(--blue);border-bottom:2px solid var(--blue);padding-bottom:4px}
.hero-title{left:80px;top:248px;font-size:48px;line-height:58px}
.hero-title .hl{color:var(--blue)}
.hero-arrow{width:46px;height:46px;border-radius:50%;display:flex;align-items:center;justify-content:center}
/* services */
.section-title{left:0;width:1200px;text-align:center;font-size:40px}
.card{position:absolute;width:374px;height:407px;background:var(--white);box-shadow:0 2px 14px rgba(0,0,0,.1)}
.card .photo{position:absolute;left:0;top:0;width:225px;height:225px;border-radius:0 0 50% 0;border-right:5px solid var(--blue);border-bottom:5px solid var(--blue)}
.card .mark{position:absolute;right:40px;top:140px;width:96px;height:96px;border-radius:50%;border:8px solid #f1f1f1}
.card h3{position:absolute;left:33px;top:270px;font-family:"Oswald",sans-serif;font-weight:500;font-size:21px;text-transform:uppercase;line-height:29px}
.card p{position:absolute;left:33px;width:310px;font-size:13px;font-weight:300;color:var(--text);line-height:25px}
/* about */
.about-kicker{left:683px;top:1878px;font-size:15px;color:var(--blue);font-weight:400}
.about-title{left:683px;top:1904px;font-size:40px}
.about-text{left:687px;width:390px;font-size:13.5px;font-weight:300;color:var(--text);line-height:27px}
/* gallery */
.tile{position:absolute}
/* quote */
.field{position:absolute;background:var(--white);border:1px solid #d8d8d8;border-radius:3px;font-size:13px;color:#777;padding:14px 14px}
/* faq */
.faq{position:absolute;left:300px;width:600px;height:60px;border-radius:30px;background:var(--white);box-shadow:0 1px 8px rgba(0,0,0,.12);display:flex;align-items:center;gap:20px;padding-left:6px;font-size:15px;color:var(--ink)}
.faq .q{width:48px;height:48px;border-radius:50%;background:var(--blue);color:var(--white);display:flex;align-items:center;justify-content:center;font-size:26px;font-weight:300}
.faq.open{border:2px solid var(--blue)}
.faq.open .q{background:var(--white);color:var(--blue);border:2px solid var(--blue)}
.faq-answer{left:341px;top:4305px;width:599px;height:122px;background:#eeeeee;font-size:13.5px;font-weight:300;color:var(--text);line-height:27px;padding:12px 34px}
/* footer */
.foot-brand{left:92px;top:5024px;display:flex;align-items:center;gap:8px;font-family:"Oswald",sans-serif;font-weight:600;font-size:22px;color:var(--white);white-space:nowrap}
.foot-brand .dot{width:32px;height:32px;border-radius:50%;background:var(--white)}
.foot-col h4{font-family:"Oswald",sans-serif;font-weight:500;font-size:16px;color:var(--white);margin-bottom:14px}
.foot-col ul{list-style:none}
.foot-col li{font-size:13.5px;color:#d6d6d6;line-height:31px;position:relative;padding-left:24px}
.foot-col li::before{content:"";position:absolute;left:0;top:13px;width:6px;height:6px;border-radius:50%;background:var(--blue)}
.contact-list li{padding-left:36px;line-height:20px;margin-bottom:22px}
.contact-list li::before{display:none}
.contact-list svg{position:absolute;left:0;top:0}
.social{width:44px;height:44px;border-radius:50%;background:var(--blue);border:2px solid var(--white)}
.copyright{left:0;top:5202px;width:1200px;height:61px;background:var(--blue);color:var(--white);font-size:13px;display:flex;align-items:center;justify-content:center}
</style>
</head>
<body>

<!-- HERO -->
<svg class="abs" style="left:0;top:0" width="1200" height="720" viewBox="0 0 1200 720" role="img" aria-label="Tall office towers in a city skyline under a cloudy sky">
  <defs>
    <linearGradient id="skyGrad" x1="0" y1="0" x2="0" y2="1">
      <stop offset="0" stop-color="#dbe6f0"/>
      <stop offset=".45" stop-color="#8fa6bd"/>
      <stop offset="1" stop-color="#2b4866"/>
    </linearGradient>
  </defs>
  <path d="M0 0 H1200 V40 C1190 330 1080 520 880 560 C700 600 620 700 440 686 C240 670 70 580 0 430 Z" fill="var(--blue)"/>
  <path d="M0 0 H1200 V20 C1180 320 1070 500 870 542 C690 580 610 680 440 668 C240 652 70 560 0 410 Z" fill="url(#skyGrad)"/>
</svg>

<div class="abs brand"><span class="dot"></span>Brightmoor Lift Inc</div>
<nav class="abs nav">
  <a class="active">HOME</a><a>ABOUT</a><a>SERVICES</a><a>GALLERY</a><a>FAQ</a><a>CONTACT</a>
</nav>
<div class="btn" style="left:952px;top:25px;width:168px;height:44px;font-size:16px;padding-left:24px">Free Quote<span class="ring" style="width:34px;height:34px"></span></div>

<h1 class="abs heading hero-title">Are you ready for an<br><span class="hl">Elevator</span> Revolution?</h1>
<div class="btn" style="left:80px;top:382px;width:192px;height:49px;font-size:16px">Contact Us<span class="ring"></span></div>

<div class="abs hero-arrow" style="left:952px;top:512px;background:var(--white);border:2px solid var(--blue)">
  <svg width="16" height="16" viewBox="0 0 16 16"><path d="M10 3 L5 8 L10 13" fill="none" stroke="var(--blue)" stroke-width="2"/></svg>
</div>
<div class="abs hero-arrow" style="left:1001px;top:484px;background:var(--blue)">
  <svg width="16" height="16" viewBox="0 0 16 16"><path d="M6 3 L11 8 L6 13" fill="none" stroke="#fff" stroke-width="2"/></svg>
</div>

<!-- SERVICES -->
<h2 class="abs heading section-title" style="top:716px">Our Services</h2>
<p class="abs lead" style="left:0;top:779px;width:1200px">Lorem Ipsum is simply dummy text of the printing and typesetting industry.<br>Lorem Ipsum has been the industry's standard.</p>

<div class="card" style="left:180px;top:883px">
  <div class="photo" role="img" aria-label="Elevator hoist machinery in blue tones" style="background:linear-gradient(135deg,#3a7fd6,#0d5fd0)"></div>
  <div class="mark"></div>
  <h3>Modernization</h3>
  <p style="top:303px">Lorem Ipsum is simply dummy text of the printing and typesetting industry. Lorem Ipsum has been the industry'.</p>
</div>
<div class="card" style="left:585px;top:883px">
  <div class="photo" role="img" aria-label="Technicians in hard hats working on an elevator control panel" style="background:linear-gradient(135deg,#8aa3bd,#2e3f66)"></div>
  <div class="mark"></div>
  <h3>Maintenance</h3>
  <p style="top:303px">Lorem Ipsum is simply dummy text of the printing and typesetting industry. Lorem Ipsum has been the industry'.</p>
</div>
<div class="card" style="left:180px;top:1329px">
  <div class="photo" role="img" aria-label="Technician in a hard hat repairing elevator equipment" style="background:linear-gradient(135deg,#9fb8c2,#3b4d70)"></div>
  <div class="mark"></div>
  <h3>Service &amp; Repair</h3>
  <p style="top:303px">Lorem Ipsum is simply dummy text of the printing and typesetting industry. Lorem Ipsum has been the industry'.</p>
</div>
<div class="card" style="left:585px;top:1329px">
  <div class="photo" role="img" aria-label="Rooftop guard rail installed on top of a building" style="background:linear-gradient(180deg,#a9b8c6,#5b5f5e)"></div>
  <div class="mark"></div>
  <h3>Top of Car Guard Rail<br>Installation</h3>
  <p style="top:333px">Lorem Ipsum is simply dummy text of the printing and typesetting industry.</p>
</div>

<!-- ABOUT -->
<svg class="abs" style="left:0;top:1803px" width="1200" height="560" viewBox="0 0 1200 560">
  <path d="M0 0 H1200 V420 C1100 390 1000 400 880 450 C760 500 640 470 520 420 C380 360 230 380 120 460 C70 500 30 520 0 540 Z" fill="var(--pale)"/>
</svg>
<div class="abs" role="img" aria-label="Looking up an illuminated elevator shaft" style="left:133px;top:1866px;width:311px;height:311px;border-radius:6px;background:radial-gradient(circle at 50% 45%,#bfe3f5,#3c6a99 45%,#1f2f4e)"></div>
<div class="abs" style="left:347px;top:2038px;width:188px;height:186px;border-radius:4px;background:var(--blue);border:4px solid var(--white);display:flex;align-items:center;justify-content:center">
  <span style="width:100px;height:100px;border-radius:50%;border:10px solid var(--white)"></span>
</div>
<div class="abs about-kicker">ABOUT US</div>
<h2 class="abs heading about-title">Brightmoor Lift</h2>
<p class="abs about-text" style="top:1971px">Lorem Ipsum is simply dummy text of the printing and typesetting industry. Lorem Ipsum has been .</p>
<p class="abs about-text" style="top:2039px">Lorem Ipsum is simply dummy text of the printing and typesetting industry. Lorem Ipsum has been the industry's standard dummy text ever since the 1500s, when an unknown printer took a galley of type.</p>
<div class="btn" style="left:687px;top:2167px;width:196px;height:47px;font-size:16px">Learn More<span class="ring"></span></div>

<!-- GALLERY -->
<h2 class="abs heading section-title" style="top:2421px">Our Gallery</h2>
<p class="abs lead" style="left:0;top:2485px;width:1200px">Lorem Ipsum is simply dummy text of the printing and typesetting industry.<br>Lorem Ipsum has been the industry's standard.</p>

<div class="tile" role="img" aria-label="Modern lobby with stainless steel elevator doors" style="left:153px;top:2592px;width:509px;height:247px;background:linear-gradient(90deg,#c9cfd4,#6e747b 55%,#b8bec3)"></div>
<div class="tile" role="img" aria-label="Person waiting beside an elevator with wood panelled walls" style="left:675px;top:2592px;width:347px;height:507px;background:linear-gradient(90deg,#9ca2a8,#b9824e 55%,#8a5a30)"></div>
<div class="tile" role="img" aria-label="Open elevator car with steel interior" style="left:153px;top:2851px;width:250px;height:248px;background:linear-gradient(180deg,#d7d9da,#7f8489)"></div>
<div class="tile" style="left:415px;top:2851px;width:247px;height:248px;background:var(--blue);display:flex;align-items:center;justify-content:center">
  <div style="position:absolute;inset:12px;border:1px solid rgba(255,255,255,.5)"></div>
  <svg width="50" height="50" viewBox="0 0 50 50"><path d="M25 0V50M0 25H50" stroke="#fff" stroke-width="1.5" opacity=".6"/></svg>
</div>
<div class="tile" role="img" aria-label="Row of elevators in a dark grey lobby with plants" style="left:153px;top:3113px;width:509px;height:247px;background:linear-gradient(180deg,#cdd0d2,#4f5458)"></div>
<div class="tile" role="img" aria-label="Pair of steel elevator doors beside glass windows" style="left:677px;top:3113px;width:347px;height:247px;background:linear-gradient(90deg,#9aa3ab,#6a5e57 60%,#a19a93)"></div>

<div class="abs heading" style="left:507px;top:3419px;font-size:17px;font-weight:500">Explore More</div>
<div class="abs" style="left:639px;top:3405px;width:50px;height:50px;border-radius:50%;background:var(--blue);display:flex;align-items:center;justify-content:center">
  <svg width="20" height="20" viewBox="0 0 20 20"><path d="M10 2V18M2 10H18" stroke="#fff" stroke-width="2"/></svg>
</div>

<!-- QUOTE -->
<svg class="abs" style="left:0;top:3370px" width="1200" height="720" viewBox="0 0 1200 720" role="img" aria-label="City buildings behind a blue overlay">
  <defs>
    <linearGradient id="quoteGrad" x1="0" y1="0" x2="1" y2="1">
      <stop offset="0" stop-color="#1a6ddb"/>
      <stop offset="1" stop-color="#0b53bd"/>
    </linearGradient>
  </defs>
  <path d="M0 140 C160 80 300 150 440 170 C620 195 720 140 860 90 C1000 30 1110 0 1200 10 V580 C1060 610 980 700 800 700 C600 700 500 610 300 600 C170 595 70 640 0 690 Z" fill="url(#quoteGrad)"/>
</svg>
<div class="abs" style="left:80px;top:3697px;font-size:15px;color:var(--white);font-weight:300">GET IN TOUCH</div>
<h2 class="abs heading" style="left:79px;top:3722px;font-size:40px;color:var(--white)">Get A Free Quote</h2>
<div class="abs" style="left:82px;top:3785px;font-size:15px;color:var(--white);font-weight:300">If you have an any Queston for Contact Us Today !</div>

<div class="field" style="left:544px;top:3653px;width:257px;height:47px">Name *</div>
<div class="field" style="left:813px;top:3653px;width:258px;height:47px">Email *</div>
<div class="field" style="left:544px;top:3714px;width:257px;height:47px">Phone *</div>
<div class="field" style="left:813px;top:3714px;width:258px;height:47px">Services *</div>
<div class="field" style="left:544px;top:3775px;width:527px;height:100px">Message *</div>
<div class="btn" style="left:709px;top:3892px;width:225px;height:47px;font-size:16px;border:2px solid var(--white)">Send A Message<span class="ring" style="width:34px;height:34px"></span></div>

<!-- FAQ -->
<h2 class="abs heading section-title" style="top:4110px;line-height:48px">Frequently Asked<br>Questions</h2>
<div class="faq open" style="top:4233px"><span class="q">?</span>Lorem Ipsum is simply dummy text of the printing and type ?</div>
<p class="abs faq-answer">Lorem Ipsum is simply dummy text of the printing and typesetting industry. Lorem Ipsum has been the industry's standard dummy text ever since the 1500s, when an unknown printer took a galley of type and scrambled.</p>
<div class="faq" style="top:4452px"><span class="q">?</span>Lorem Ipsum is simply dummy text of the printing ?</div>
<div class="faq" style="top:4522px"><span class="q">?</span>Lorem Ipsum is simply dummy text of the printing &amp; type ?</div>
<div class="faq" style="top:4595px"><span class="q">?</span>Lorem Ipsum is simply dummy text and type ?</div>

<!-- FOOTER -->
<svg class="abs" style="left:0;top:4750px" width="1200" height="460" viewBox="0 0 1200 460" role="img" aria-label="Night city skyline with a tall tower in dark tones">
  <path d="M0 120 C120 70 260 40 420 80 C560 115 640 140 760 110 C900 70 1000 20 1100 10 C1150 5 1180 10 1200 20 V460 H0 Z" fill="var(--blue)"/>
  <path d="M0 140 C120 90 260 60 420 100 C560 135 640 160 760 130 C900 90 1000 40 1100 30 C1150 25 1180 30 1200 40 V460 H0 Z" fill="var(--dark)"/>
</svg>
<div class="abs foot-brand"><span class="dot"></span>Brightmoor Lift Inc</div>
<div class="abs" style="left:135px;top:5084px;display:flex;gap:8px">
  <span class="social"></span><span class="social"></span><span class="social"></span>
</div>

<div class="abs foot-col" style="left:345px;top:4918px">
  <h4>SITEMAP</h4>
  <ul><li>Home</li><li>About</li><li>Services</li><li>Gallery</li><li>Faq</li><li>Contact</li></ul>
</div>
<div class="abs foot-col" style="left:611px;top:4918px">
  <h4>SERVICES</h4>
  <ul><li>Modernization</li><li>Maintenance</li><li>Service &amp; Repair</li><li>Top Of Car Guard Rail Installation</li></ul>
</div>
<div class="abs foot-col" style="left:877px;top:4918px;width:260px">
  <h4>CONTACT US</h4>
  <ul class="contact-list">
    <li><svg width="20" height="20" viewBox="0 0 24 24"><path d="M6.6 10.8a15 15 0 0 0 6.6 6.6l2.2-2.2a1 1 0 0 1 1-.25 11.4 11.4 0 0 0 3.6.57 1 1 0 0 1 1 1V20a1 1 0 0 1-1 1A17 17 0 0 1 3 4a1 1 0 0 1 1-1h3.5a1 1 0 0 1 1 1 11.4 11.4 0 0 0 .57 3.6 1 1 0 0 1-.25 1z" fill="var(--blue)"/></svg>(416) 555 0142</li>
    <li><svg width="20" height="20" viewBox="0 0 24 24"><path d="M6.6 10.8a15 15 0 0 0 6.6 6.6l2.2-2.2a1 1 0 0 1 1-.25 11.4 11.4 0 0 0 3.6.57 1 1 0 0 1 1 1V20a1 1 0 0 1-1 1A17 17 0 0 1 3 4a1 1 0 0 1 1-1h3.5a1 1 0 0 1 1 1 11.4 11.4 0 0 0 .57 3.6 1 1 0 0 1-.25 1z" fill="var(--blue)"/></svg>(905) 555 0187</li>
    <li><svg width="20" height="20" viewBox="0 0 24 24"><rect x="2" y="5" width="20" height="14" rx="2" fill="var(--blue)"/><path d="M3 6l9 7 9-7" fill="none" stroke="var(--dark)" stroke-width="1.6"/></svg>info@brightmoorlift.ca</li>
  </ul>
</div>
<div class="btn" style="left:869px;top:5106px;width:167px;height:47px;font-size:16px;padding-left:24px">Free Quote<span class="ring" style="width:34px;height:34px"></span></div>

<div class="abs copyright">©Brightmoor Lift - 2020 All rights reserved.</div>

</body>
</html>
```